Business card design Needed for new logo / Construction business, home extensions and new builds

We need a business card design using our new logo files which i will attach to this project :)

We are a small construction business specialising in home extensions, new builds and property development. We are very ambitious and would appreciate professional and elegant designs for our new business card.

Very serious about using the services on MakerQuarry and recently acquired our new logo from here :)

Please get involved, i will feedback when i can as i am very busy but can respond daily, thanks

Target Market(s)

People that want to build onto their houses, new building developments or adding too their existing property

Industry/Entity Type

Construction

Contact Information for Business Card

Renwick Tolliver Construction, Lionel Ashby (Managing Director), Tel 07822254961, email - info@renwick-tolliver, www.renwick-tolliver.co.uk

Colors

Designer to choose colors to be used in the design.

Requirements
Must have
• I like a deep grey on the back please. A lot of you have provided black from and back, try mixing things up a little. The black looks cool 😎 Thanks

```html
<!DOCTYPE html>
<html lang="en">
<head>
<meta charset="utf-8">
<title>Renwick Tolliver Construction – Business Card</title>
<link rel="stylesheet" href="https://fonts.googleapis.com/css2?family=Cinzel:wght@500&family=Open+Sans:wght@400;600&display=swap">
<style>
  :root {
    --backdrop: #2c2c2f;
    --card-front: #1b1b1d;
    --card-back: #27272a;
    --emboss-front: #232326;
    --emboss-back: #313135;
    --silver: #cfcfd1;
    --text-light: #ececec;
    --gold: #d4a133;
    --gold-light: #f0cf72;
    --gold-dark: #9c6f1c;
  }
  * { box-sizing: border-box; margin: 0; padding: 0; }
  html, body { width: 1200px; height: 780px; overflow: hidden; }
  body {
    background: var(--backdrop);
    font-family: "Open Sans", Arial, sans-serif;
    position: relative;
  }
  .card {
    position: absolute;
    top: 240px;
    width: 525px;
    height: 300px;
    overflow: hidden;
    border-radius: 2px;
    box-shadow: 0 10px 28px rgba(0,0,0,.45);
  }
  .card--front { left: 50px; background: var(--card-front); }
  .card--back  { left: 625px; background: var(--card-back); }

  /* large embossed brand decoration on the front */
  .emboss-name {
    position: absolute;
    left: 26px;
    top: 22px;
    font-family: "Cinzel", Georgia, serif;
    font-weight: 500;
    font-size: 44px;
    line-height: 1.05;
    letter-spacing: 1px;
    color: var(--emboss-front);
  }

  /* brand lockup */
  .brand {
    position: absolute;
    display: flex;
    align-items: center;
    gap: 10px;
    font-family: "Cinzel", Georgia, serif;
    font-weight: 500;
    text-align: right;
  }
  .brand__mark { width: 26px; height: 26px; background: var(--gold); flex: none; }
  .brand__name { color: var(--silver); font-size: 15px; line-height: 1.2; letter-spacing: 1px; }
  .brand--front { right: 34px; top: 34px; flex-direction: row-reverse; }

  .contact {
    position: absolute;
    right: 46px;
    top: 104px;
    text-align: right;
  }
  .contact__name {
    font-weight: 600;
    font-size: 30px;
    line-height: 1.1;
  }
  .contact__first { color: var(--silver); }
  .contact__last { color: var(--gold); }
  .contact__role {
    color: var(--text-light);
    font-size: 14px;
    margin-top: 4px;
  }
  .contact__list { list-style: none; margin-top: 22px; }
  .contact__item {
    display: flex;
    justify-content: flex-end;
    align-items: center;
    gap: 8px;
    color: var(--text-light);
    font-size: 13px;
    line-height: 22px;
  }
  .contact__icon { width: 13px; height: 13px; flex: none; }

  .gold-steps { position: absolute; right: 0; top: 150px; width: 32px; }
  .gold-steps span {
    display: block;
    height: 10px;
    margin-left: auto;
    margin-bottom: 3px;
    background: linear-gradient(180deg, var(--gold-light), var(--gold) 55%, var(--gold-dark));
  }
  .gold-steps span:nth-child(1) { width: 16px; }
  .gold-steps span:nth-child(2) { width: 24px; }
  .gold-steps span:nth-child(3) { width: 32px; }
  .gold-steps span:nth-child(4) { width: 24px; }

  /* back */
  .brand--back {
    left: 50%;
    top: 50%;
    transform: translate(-50%, -50%);
    flex-direction: column;
    text-align: center;
    gap: 14px;
  }
  .brand--back .brand__mark { width: 34px; height: 34px; background: var(--emboss-back); }
  .brand--back .brand__name { color: var(--emboss-back); font-size: 26px; letter-spacing: 2px; }
</style>
</head>
<body>

<section class="card card--front" aria-label="Business card front">
  <div class="emboss-name" aria-hidden="true">Renwick<br>Tolliver</div>

  <div class="brand brand--front">
    <span class="brand__mark"></span>
    <span class="brand__name">Renwick Tolliver<br>Construction</span>
  </div>

  <div class="contact">
    <p class="contact__name"><span class="contact__first">Lionel</span> <span class="contact__last">Ashby</span></p>
    <p class="contact__role">Managing Director</p>
    <ul class="contact__list">
      <li class="contact__item">0782 225 4961
        <svg class="contact__icon" viewBox="0 0 16 16" aria-hidden="true"><path fill="#d4a133" d="M3.6 1.5l2.3 2.6-1.3 1.7c.9 2 2.6 3.8 4.7 4.8l1.7-1.3 2.6 2.3-1.4 2.4C7.3 13.6 2.4 8.7 1.2 3z"/></svg>
      </li>
      <li class="contact__item">info@renwick-tolliver.co.uk
        <svg class="contact__icon" viewBox="0 0 16 16" aria-hidden="true"><circle cx="8" cy="8" r="6.5" fill="none" stroke="#d4a133" stroke-width="1.6"/><path d="M1.5 8h13M8 1.5c-3 3.5-3 9.5 0 13M8 1.5c3 3.5 3 9.5 0 13" fill="none" stroke="#d4a133" stroke-width="1.2"/></svg>
      </li>
      <li class="contact__item">www.renwick-tolliver.co.uk
        <svg class="contact__icon" viewBox="0 0 16 16" aria-hidden="true"><rect x="1.5" y="3.5" width="13" height="9" fill="none" stroke="#d4a133" stroke-width="1.6"/><path d="M1.5 3.5L8 9l6.5-5.5" fill="none" stroke="#d4a133" stroke-width="1.4"/></svg>
      </li>
    </ul>
  </div>

  <div class="gold-steps" aria-hidden="true"><span></span><span></span><span></span><span></span></div>
</section>

<section class="card card--back" aria-label="Business card back">
  <div class="brand brand--back">
    <span class="brand__mark"></span>
    <span class="brand__name">Renwick Tolliver<br>Construction</span>
  </div>
</section>

</body>
</html>
```